Design a Cover for a Book on Innovation

I need a design for my book: The Quiet Harvest of Invention
It is about the following:

Innovation is not just for those endowed with special talent or skills in technology. This book describes the thought framework that consists of seven principal differences between the current period and the past. Innovation is happening along these shifts. Understanding the differences can allow for consistent innovation and the identification of real opportunities.
Updates

To All: All of you show great talent as designers. I've added a bit more to the description. Feel free to ask questions. Best, DT

Font styles to use
Sans Serif

Colors

Designer to choose colors to be used in the design.

Requirements
Must have
• It should feel modern and innovative. It should incorporate the meaning of Quiet Harvest.
Nice to have
• It should have the title, and a holder spot for the subtitle and author's name Dara Tovens
Should not have
• It should not be overly busy. Sleek modern design that still gets the point across. Alternatively an image that is a full cover graphic.

```html
<!DOCTYPE html>
<html lang="en">
<head>
<meta charset="utf-8">
<title>The Quiet Harvest of Invention — Cover</title>
<link rel="stylesheet" href="https://fonts.googleapis.com/css2?family=Poppins:ital,wght@0,200;0,300;1,300&display=swap">
<style>
  :root {
    --paper: #f4f4f2;
    --ink: #333333;
    --accent-red: #a10d0d;
    --rule: #6a6a6a;
    --leaf-green: #8aa84a;
    --leaf-deep: #4f7a22;
    --glass: #ffffff;
  }
  html, body {
    margin: 0;
    padding: 0;
    width: 1200px;
    height: 1088px;
    overflow: hidden;
    background: var(--paper);
  }
  .cover {
    position: relative;
    width: 1200px;
    height: 1088px;
    overflow: hidden;
    background: var(--paper);
    font-family: "Poppins", sans-serif;
  }
  .book-title { margin: 0; font-weight: inherit; font-size: inherit; }
  .title-line {
    position: absolute;
    right: 398px;
    margin: 0;
    line-height: 1;
    white-space: nowrap;
    text-align: right;
  }
  .title-the     { top: 100px; font-size: 104px; font-weight: 200; color: var(--ink); }
  .title-quiet   { top: 198px; font-size: 104px; font-weight: 200; color: var(--ink); }
  .title-harvest { top: 340px; font-size: 144px; font-weight: 300; color: var(--accent-red); }
  .title-of      { top: 570px; font-size: 88px;  font-weight: 200; color: var(--ink); }
  .title-invention {
    top: 636px;
    font-size: 160px;
    font-weight: 300;
    color: var(--accent-red);
    letter-spacing: -1px;
  }
  .title-invention .initial {
    font-size: 272px;
    font-weight: 200;
    line-height: 0;
  }
  .cover-illustration {
    position: absolute;
    left: 820px;
    top: 0;
    width: 270px;
    height: 795px;
    border-radius: 0 0 135px 135px;
    background: linear-gradient(180deg,
      rgba(79,122,34,0.0) 0%,
      rgba(79,122,34,0.35) 30%,
      var(--leaf-green) 52%,
      #c9d3b4 66%,
      var(--glass) 88%,
      #e6e6e2 100%);
  }
  .baseline-rule {
    position: absolute;
    left: 0;
    top: 774px;
    width: 1200px;
    height: 0;
    border-top: 1.5px solid var(--rule);
  }
  .subtitle {
    position: absolute;
    left: 0;
    top: 902px;
    width: 1200px;
    margin: 0;
    text-align: center;
    font-size: 31px;
    font-weight: 300;
    font-style: italic;
    color: var(--ink);
    text-decoration: underline;
    text-decoration-thickness: 1.5px;
    text-underline-offset: 6px;
    white-space: nowrap;
  }
  .author {
    position: absolute;
    left: 0;
    top: 990px;
    width: 1200px;
    margin: 0;
    text-align: center;
    font-size: 32px;
    font-weight: 300;
    letter-spacing: 6px;
    color: var(--accent-red);
    white-space: nowrap;
  }
  .bottom-rule {
    position: absolute;
    left: 0;
    top: 1084px;
    width: 1200px;
    height: 0;
    border-top: 2px solid var(--ink);
  }
</style>
</head>
<body>
  <main class="cover">
    <div class="cover-illustration" role="img" aria-label="A green fruit cap with a stem and leaf resting on a glowing glass light bulb"></div>

    <h1 class="book-title" aria-label="The Quiet Harvest of Invention">
      <span class="title-line title-the">The</span>
      <span class="title-line title-quiet">Quiet</span>
      <span class="title-line title-harvest">Harvest</span>
      <span class="title-line title-of">of</span>
      <span class="title-line title-invention"><span class="initial">I</span>nvention</span>
    </h1>

    <div class="baseline-rule"></div>

    <p class="subtitle">A FRAMEWORK TO SIMPLIFY THE MODERN AGE OF INVENTION</p>
    <p class="author">DARA TOVENS</p>

    <div class="bottom-rule"></div>
  </main>
</body>
</html>
```